Bold, Modern, Clean "Kestrelwaymassage.com" website

Why we stand out?
We are a male and female mobile massage team. Our names are Paul and Lina. 
Kestrel Way is a Seattle based mobile massage service. Our massage is offered to the community with a goal of facilitating balance within each individual. We specialize in integrated Pain management, and sports/medical massage therapy. Every client's first assessment is attended by our male and female massage therapist team. Depending on the goals identified for an individual determines which therapist will be assigned to provide treatment, if not both.

Our passion...
Here at Kestrel Way, we have a great passion for Postural Resoration and how it is integrated into an individual's Massage treatment. We pride ourselves in being natural facilitators of healing, which takes the ego of the therapist out of the client's healing process. We strive to deliver the best massage possible by including modalities such as Neuromuscular, Myofascial release, spontaneous muscle release, postural restoration, orthopedic, and medical massage.

Our education...

We are both Graduates of Venmora, school of massage therapy. We have continuing education in medical massage, myofacial release, trigger point therapy, postural restoration, anatomy, and spontaneous muscle release. Lina is also a Certified Yoga Instructor, which amplifies her experience with flexibility and strength as it pertains to each individual. Paul's passion is Massage, stretching, and strength training to encourage postural restoration and realignment.

Our rates-

Our rates are $75/ 60 minutes, $95/ 90 minutes, and $120/ 120 minutes.

Education-
Both Lina and I worked as behavioral health professionals that specialized in life skills mentoring for youth who had experienced different types of trauma. This led us both to want to help others in a different environment, where individuals can be empowered to take responsibility over their own healing. To us, massage is a type of manipulation physical therapy, that encourages healing on many levels.

Advice to any massage client-
The most important thing to 'us', as Licenced providers is to get you on to our table to show you our skills. But a good therapist never forgets that it's not about what we do for you, but what we can facilitate for you. Your health and healing has nothing to do with us. It is yours, not ours. Identify what your goals are with any Therapist, and know what the end looks like. Progress should be tangible, such as range of motion, and decreased pain.

Lina and Paul at Kestrel Way are awesome! I recently had open heart surgery, and Lina worked on me to increase my range of motion while helping with the pinched nerve from my arm being in the same position for so long during my surgery. My wife drives a lot for work, and Paul has helped decrease her neck and lower back pain immensely. They are seriously the best therapists I have ever worked with. I would recommend them to anyone who needs anything from stress relief to a medical massage treatment. They are professional, up beat, easy going, and always on time. And, I love that they meet us where ever we like! We did a staycation recently, where they came to our hotel to give us relaxation massages. Although usually they come to our home, where we focus on pain related issues. We will continue to work with them for a long, long time.

Target Market(s)

Mobile massage therapy clients

Industry/Entity Type

Massage Therapy

Coding

Coded - Design and coding required

Number of Pages Required

1 page

Font styles to use
Serif
Sans Serif

Requirements
Must have
• Please add or remove any information that would help the presentation of our website. Our logo is posted below, please include into the website.
• Please include a contact field that includes, kestrelwaymassage@fernmail.net,
• (206) 555-0148
• We have also included our own stock photos, as well as a photo of Paul and Lina. Please include a cropped photo of both massage therapists.

```html
<!DOCTYPE html>
<html lang="en">
<head>
<meta charset="utf-8">
<title>Kestrel Way Mobile Massage</title>
<link href="https://fonts.googleapis.com/css2?family=Open+Sans:ital,wght@0,400;0,600;0,700;0,800;1,400&display=swap" rel="stylesheet">
<style>
:root{
  --navy:#173f8f;
  --navy-deep:#0f2d6e;
  --royal:#1c4aa3;
  --cyan:#1fb8e8;
  --ink:#444444;
  --text:#6a6a6a;
  --line:#e1e1e1;
  --white:#ffffff;
  --band:#efefef;
}
*{box-sizing:border-box;margin:0;padding:0}
html,body{width:1200px;height:2169px;overflow:hidden}
body{position:relative;background:var(--white);font-family:"Open Sans",Arial,sans-serif;color:var(--text)}
.abs{position:absolute}

.top-bar{left:0;top:0;width:1200px;height:7px;background:linear-gradient(90deg,var(--navy-deep),var(--royal) 50%,var(--navy-deep))}
.site-header{left:0;top:7px;width:1200px;height:125px;background:var(--white)}
.brand{left:160px;top:36px;width:158px;height:158px;border-radius:50%;background:radial-gradient(circle at 40% 35%,#2f63c2,var(--navy-deep) 75%);border:6px solid var(--white);box-shadow:0 0 0 3px var(--navy);z-index:5;display:flex;align-items:center;justify-content:center;text-align:center}
.brand span{color:var(--white);font-weight:800;font-size:24px;line-height:1.05;text-transform:uppercase;letter-spacing:.5px}
.quick-contact{left:738px;top:30px;display:flex;align-items:center;gap:14px;font-size:16px;font-weight:700;color:#333}
.quick-contact .phone-dot{width:32px;height:32px;border-radius:50%;background:var(--navy);display:flex;align-items:center;justify-content:center}
.quick-contact b{color:var(--navy)}
.main-nav{top:90px;left:0;width:1200px;font-size:13px;font-weight:600;color:#444;text-transform:uppercase}
.main-nav a{position:absolute;color:inherit;text-decoration:none;white-space:nowrap}
.main-nav a.is-current{color:var(--navy)}
.nav-pointer{left:481px;top:121px;width:0;height:0;border-left:13px solid transparent;border-right:13px solid transparent;border-bottom:11px solid var(--navy);z-index:4}

.hero{left:0;top:132px;width:1200px;height:565px;background:linear-gradient(100deg,#3a3f44 0%,#245c86 22%,#1a5f94 35%,#6b5a4e 55%,#8a8478 72%,#6e7466 88%,#4c5249 100%)}
.hero-shade{left:0;top:132px;width:1200px;height:565px;background:linear-gradient(90deg,rgba(0,0,0,.35),rgba(0,0,0,.05) 50%,rgba(0,0,0,.25))}
.hero-title{left:163px;top:340px;color:var(--white);font-weight:700;font-size:34px;line-height:38px;text-transform:uppercase;letter-spacing:.5px}
.hero-copy{left:163px;top:439px;width:320px;color:var(--white);font-size:11px;line-height:18px}
.hero-arrow{top:388px}
.quick-form{left:750px;top:227px;width:285px;height:382px;border:2px solid var(--white);background:rgba(0,0,0,.55)}
.quick-form h2{position:absolute;left:0;top:20px;width:100%;text-align:center;color:var(--white);font-size:17px;font-weight:700;text-transform:uppercase}
.field{position:absolute;left:20px;width:243px;height:35px;background:var(--white);border-radius:2px;font-size:10px;font-style:italic;color:#777;padding:11px 9px}
.field.message{height:82px}
.btn{display:flex;align-items:center;justify-content:center;gap:5px;background:linear-gradient(var(--royal),var(--navy-deep));color:var(--white);font-weight:700;text-transform:uppercase;border-radius:2px;border-bottom:2px solid #0a2357}
.form-submit{position:absolute;left:20px;top:320px;width:101px;height:40px;font-size:12px}
.btn svg{flex:none}

.service{width:272px}
.service .thumb{width:272px;height:160px;border:3px solid #f1f1f1;box-shadow:0 0 0 1px #dcdcdc}
.service h3{position:absolute;left:0;top:188px;font-size:18px;font-weight:600;color:var(--ink);text-transform:uppercase;white-space:nowrap}
.service p{position:absolute;left:0;top:211px;width:272px;font-size:10.5px;line-height:19px}
.service .btn{position:absolute;left:0;top:277px;width:95px;height:31px;font-size:10px}

.stars-band{left:0;top:1110px;width:1200px;height:358px;background:linear-gradient(90deg,#f2f2f2,#ececec 45%,#e9e9e9)}
.stars-photo{left:600px;top:1110px;width:600px;height:358px;background:linear-gradient(90deg,rgba(236,236,236,0),#e8dcd2 35%,#d4b8a6 60%,#efece8 85%,#f7f7f7)}
.stars-title{left:160px;top:1180px;font-size:22px;font-weight:700;color:var(--ink);text-transform:uppercase}
.stars-copy{left:160px;top:1223px;width:405px;font-size:10.5px;line-height:19.5px}
.stars-rating{left:163px;top:1340px;display:flex;gap:4px}
.stars-btn{left:160px;top:1378px;width:95px;height:31px;font-size:10px}

.rates-title{left:0;top:1502px;width:1200px;text-align:center;font-size:22px;font-weight:700;color:var(--ink);text-transform:uppercase}
.rates-intro{left:0;top:1552px;width:1200px;text-align:center;font-size:10.5px;line-height:18px}
.rate{width:318px;text-align:center}
.rate .disc{margin:0 auto;width:156px;height:156px;border-radius:50%;border:4px solid var(--white);box-shadow:0 0 0 3px var(--navy);background:radial-gradient(circle at 35% 30%,#3d73d2,#1d4aa6 45%,#0d2563 90%);display:flex;flex-direction:column;align-items:center;justify-content:center;color:var(--white)}
.rate .price{font-size:34px;font-weight:800;line-height:34px}
.rate .duration{font-size:13px;font-weight:700;text-transform:uppercase;margin-top:2px}
.rate h3{margin-top:24px;font-size:19px;font-weight:600;color:var(--ink);text-transform:uppercase}
.rate p{margin:14px auto 0;width:260px;font-size:10.5px;line-height:18.5px}
.rate-divider{top:1627px;width:1px;height:238px;background:var(--line)}

.site-footer{left:0;top:1899px;width:1200px;height:270px;background:radial-gradient(ellipse at 30% 40%,#2355b0,transparent 60%),radial-gradient(ellipse at 80% 70%,#1b4aa0,transparent 55%),var(--navy);color:var(--white)}
.footer-brand{left:160px;top:1948px;width:110px;height:110px;border-radius:50%;border:4px solid var(--white);background:var(--navy-deep);display:flex;align-items:center;justify-content:center;text-align:center}
.footer-brand span{color:var(--white);font-weight:800;font-size:16px;line-height:1.05;text-transform:uppercase}
.footer-col h4{font-size:14px;font-weight:600;text-transform:uppercase;color:var(--white)}
.footer-col p,.footer-col li{font-size:11px;line-height:18px;color:#e6ecf8}
.contact-list{list-style:none;margin-top:10px}
.contact-list li{display:flex;align-items:center;gap:12px;margin-bottom:5px}
.news-input{left:607px;top:2014px;width:204px;height:33px;background:var(--white);font-size:10px;color:#555;padding:10px 10px}
.news-btn{left:811px;top:2014px;width:70px;height:33px;background:var(--cyan);color:var(--white);font-size:11px;font-weight:700;text-transform:uppercase;display:flex;align-items:center;justify-content:center}
.social-list{list-style:none;margin-top:12px}
.social-list li{display:flex;align-items:center;gap:12px;height:24.5px;font-size:11px}
.social-list i{width:7px;height:7px;border-radius:50%;background:var(--white)}
.footer-rule{left:62px;top:2100px;width:1076px;height:1px;background:rgba(255,255,255,.18)}
.footer-bottom{left:0;top:2126px;width:1200px;text-align:center;font-size:10.5px;color:#e6ecf8;word-spacing:1px}
.footer-bottom span{margin:0 5px}
</style>
</head>
<body>

<div class="abs top-bar"></div>
<header class="abs site-header"></header>
<div class="abs brand"><span>Kestrel<br>Way</span></div>

<div class="abs quick-contact">
  <span class="phone-dot"><svg width="16" height="16" viewBox="0 0 24 24"><path fill="#fff" d="M6.6 10.8c1.4 2.8 3.8 5.1 6.6 6.6l2.2-2.2c.3-.3.7-.4 1-.2 1.1.4 2.3.6 3.6.6.6 0 1 .4 1 1V20c0 .6-.4 1-1 1C10.6 21 3 13.4 3 4c0-.6.4-1 1-1h3.5c.6 0 1 .4 1 1 0 1.3.2 2.5.6 3.6.1.3 0 .7-.2 1z"/></svg></span>
  <span>QUICK CONTACT - <b>(206) 555-0148</b></span>
</div>

<nav class="abs main-nav">
  <a class="is-current" style="left:474px">Home</a>
  <a style="left:559px">Our Passion</a>
  <a style="left:691px">Our Education</a>
  <a style="left:842px">Our Rates</a>
  <a style="left:957px">Contact Us</a>
</nav>
<div class="abs nav-pointer"></div>

<section>
  <div class="abs hero" role="img" aria-label="Therapist in a blue tunic massaging a client's back on a table beside a bright window"></div>
  <div class="abs hero-shade"></div>
  <h1 class="abs hero-title">Kestrel Way<br>Mobile Massage</h1>
  <p class="abs hero-copy">Lorem ipsum dolor sit amet, consectetur adipiscing elit, sed do eiusmod tempor incididunt ut labore et dolore magna aliqua. Ut enim ad minim veniam.</p>
  <svg class="abs hero-arrow" style="left:30px" width="28" height="54" viewBox="0 0 28 54"><path d="M26 1 2 27l24 26" fill="none" stroke="#fff" stroke-width="1.5"/></svg>
  <svg class="abs hero-arrow" style="left:1128px" width="28" height="54" viewBox="0 0 28 54"><path d="M2 1l24 26L2 53" fill="none" stroke="#fff" stroke-width="1.5"/></svg>

  <form class="abs quick-form">
    <h2>Quick Contact Form</h2>
    <div class="field" style="top:60px">Company Name</div>
    <div class="field" style="top:102px">Title</div>
    <div class="field" style="top:144px">Mobile</div>
    <div class="field" style="top:186px">Email</div>
    <div class="field message" style="top:228px">Message:</div>
    <div class="btn form-submit">Submit <svg width="10" height="10" viewBox="0 0 10 10"><circle cx="5" cy="5" r="4" fill="none" stroke="#fff" stroke-width="1.2"/><path d="M4 3l2 2-2 2" fill="none" stroke="#fff" stroke-width="1.2"/></svg></div>
  </form>
</section>

<section>
  <article class="abs service" style="left:160px;top:736px">
    <div class="thumb" role="img" aria-label="Therapist working on a client's upper back and shoulder" style="background:linear-gradient(120deg,#5a4a44,#9a7b6a 45%,#c9a898 70%,#e9e4e2)"></div>
    <h3>Neuromuscular</h3>
    <p>Sed ut perspiciatis unde omnis iste natus error sit voltatem accusantium doloremptatem accusanti um doloremque laudantium, totam.</p>
    <div class="btn">Read More <svg width="9" height="9" viewBox="0 0 10 10"><circle cx="5" cy="5" r="4" fill="none" stroke="#fff" stroke-width="1.2"/><path d="M4 3l2 2-2 2" fill="none" stroke="#fff" stroke-width="1.2"/></svg></div>
  </article>
  <article class="abs service" style="left:463px;top:736px">
    <div class="thumb" role="img" aria-label="Hands applying myofascial release to a client's back" style="background:linear-gradient(120deg,#d9d2cc,#c79f86 40%,#a87560 70%,#e5ddd6)"></div>
    <h3>Myofascial Release</h3>
    <p>Sed ut perspiciatis unde omnis iste natus error sit voltatem accusantium doloremptatem accusanti um doloremque laudantium, totam.</p>
    <div class="btn">Read More <svg width="9" height="9" viewBox="0 0 10 10"><circle cx="5" cy="5" r="4" fill="none" stroke="#fff" stroke-width="1.2"/><path d="M4 3l2 2-2 2" fill="none" stroke="#fff" stroke-width="1.2"/></svg></div>
  </article>
  <article class="abs service" style="left:766px;top:736px">
    <div class="thumb" role="img" aria-label="Therapist in blue uniform giving a medical massage" style="background:linear-gradient(120deg,#1f5d8f,#3a78a8 40%,#a58a78 70%,#cfd6c8)"></div>
    <h3>Medical Massage</h3>
    <p>Sed ut perspiciatis unde omnis iste natus error sit voltatem accusantium doloremptatem accusanti um doloremque laudantium, totam.</p>
    <div class="btn">Read More <svg width="9" height="9" viewBox="0 0 10 10"><circle cx="5" cy="5" r="4" fill="none" stroke="#fff" stroke-width="1.2"/><path d="M4 3l2 2-2 2" fill="none" stroke="#fff" stroke-width="1.2"/></svg></div>
  </article>
</section>

<section>
  <div class="abs stars-band"></div>
  <div class="abs stars-photo" role="img" aria-label="Client lying face down receiving a back massage on a white towel"></div>
  <h2 class="abs stars-title">5/5 Stars Massage Therapy</h2>
  <p class="abs stars-copy">Sed ut perspiciatis unde omnis iste natus error sit voluptatem accusantium do-loremque laudantium, totam rem aperiam, eaque ipsa quae ab illo inventore verit atis et quasi architecto beatae vitae dicta sunt explicaemo enim ipsam voluptatem quia voluptas sit aspernatur aut odit aut fugit, sed quia consequuntur gni dolores eos qui ratione voluptatem sequi nesciunt. Neque porro quisquam</p>
  <div class="abs stars-rating">
    <svg width="86" height="16" viewBox="0 0 86 16"><g fill="#c8c8c8"><path id="st" d="M8 0l2.4 5 5.6.7-4 3.9 1 5.5L8 12.4 3 15.1l1-5.5-4-3.9L5.6 5z"/><use href="#st" x="17.5"/><use href="#st" x="35"/><use href="#st" x="52.5"/><use href="#st" x="70"/></g></svg>
  </div>
  <div class="abs btn stars-btn">Read More <svg width="9" height="9" viewBox="0 0 10 10"><circle cx="5" cy="5" r="4" fill="none" stroke="#fff" stroke-width="1.2"/><path d="M4 3l2 2-2 2" fill="none" stroke="#fff" stroke-width="1.2"/></svg></div>
</section>

<section>
  <h2 class="abs rates-title">Our Rates</h2>
  <p class="abs rates-intro">Sed ut perspiciatis unde omnis iste natus error sit voluptatem accusantiumolo<br>remque laudantium, totam rem aperiam, eaque ipsa quae ab illo</p>
  <div class="abs rate-divider" style="left:441px"></div>
  <div class="abs rate-divider" style="left:763px"></div>
  <div class="abs rate" style="left:122px;top:1605px">
    <div class="disc"><span class="price">$75/</span><span class="duration">60 Minutes</span></div>
    <h3>Education</h3>
    <p>Sed ut perspiciatis unde omnis iste natus error voluptatem accusantiumolo remque laudantium, totam rem aperiam, eaque ipsa quae ab illo</p>
  </div>
  <div class="abs rate" style="left:441px;top:1605px">
    <div class="disc"><span class="price">$95/</span><span class="duration">90 Minutes</span></div>
    <h3>Education</h3>
    <p>Sed ut perspiciatis unde omnis iste natus error voluptatem accusantiumolo remque laudantium, totam rem aperiam, eaque ipsa quae ab illo</p>
  </div>
  <div class="abs rate" style="left:759px;top:1605px">
    <div class="disc"><span class="price">$120/</span><span class="duration">120 Minutes</span></div>
    <h3>Education</h3>
    <p>Sed ut perspiciatis unde omnis iste natus error voluptatem accusantiumolo remque laudantium, totam rem aperiam, eaque ipsa quae ab illo</p>
  </div>
</section>

<footer>
  <div class="abs site-footer"></div>
  <div class="abs footer-brand"><span>Kestrel<br>Way</span></div>

  <div class="abs footer-col" style="left:341px;top:1935px">
    <h4>Contact Us</h4>
    <p style="margin-top:12px">88a Alder Row, Seattle<br>Washington WA 98109</p>
    <ul class="contact-list">
      <li><svg width="16" height="16" viewBox="0 0 24 24"><path fill="none" stroke="#fff" stroke-width="1.6" d="M6.6 10.8c1.4 2.8 3.8 5.1 6.6 6.6l2.2-2.2c.3-.3.7-.4 1-.2 1.1.4 2.3.6 3.6.6.6 0 1 .4 1 1V20c0 .6-.4 1-1 1C10.6 21 3 13.4 3 4c0-.6.4-1 1-1h3.5c.6 0 1 .4 1 1 0 1.3.2 2.5.6 3.6.1.3 0 .7-.2 1z"/></svg>(206) 555-0192</li>
      <li><svg width="16" height="12" viewBox="0 0 16 12"><rect x=".8" y=".8" width="14.4" height="10.4" fill="none" stroke="#fff" stroke-width="1.3"/><path d="M1 1l7 6 7-6" fill="none" stroke="#fff" stroke-width="1.3"/></svg>hello@kestrelwaymassage.com</li>
    </ul>
  </div>

  <div class="abs footer-col" style="left:606px;top:1935px">
    <h4>Newsletter</h4>
    <p style="margin-top:10px;font-size:10px;width:250px">Excepteur sint occaecat cupidatat non proident, sunt in culpa qui officia deserunt mollit anim</p>
  </div>
  <div class="abs news-input">Enter your email address</div>
  <div class="abs news-btn">Sign Up</div>

  <div class="abs footer-col" style="left:959px;top:1928px">
    <h4>Social</h4>
    <ul class="social-list">
      <li><i></i>Friendwall</li>
      <li><i></i>Chirpline</li>
      <li><i></i>Circlenet</li>
      <li><i></i>Reelcast</li>
    </ul>
  </div>

  <div class="abs footer-rule"></div>
  <p class="abs footer-bottom"><span>Home</span><span>About</span><span>Advertise With Us</span><span>Privacy Policy</span><span>Terms of Service</span><span>© 2015 Kestrel Way Massage. All Rights Reserved</span></p>
</footer>

</body>
</html>
```